Business Card for premium dental clinic

We are a premium dental clinic based in Brasov, Romania with more than 15 year on the market, providing quality dental treatment made by a team of more specialized dentists, working with modern equipment as a solution to beautiful and healthy teeth.

Our current logo for the clinic use 2 square with colors black and gold - dr Ternisu - lumen, using family fonts Bodoni, Myriad Pro and Segoe Print.
Depending on the printing we used some gold CMYK background or gold foil picture background or a gold gradient.
We want a business card:
- eye catching business card
- distinguished business card
- premium design
- to keep the color scheme of black and gold
- to attract the customers to spent time reading the information
- modern concept

```html
<!DOCTYPE html>
<html lang="en">
<head>
<meta charset="utf-8">
<title>Lumen Dental Clinic – Business Card</title>
<link rel="stylesheet" href="https://fonts.googleapis.com/css2?family=Montserrat:wght@400&family=Oswald:wght@400&display=swap">
<style>
  :root{
    --backdrop:#e6e7e9;
    --card-black:#050708;
    --white:#ffffff;
    --gold:#e6b43a;
    --gold-light:#f4ea74;
    --gold-deep:#c1822f;
    --gold-warm:#fbd24a;
    --address-yellow:#f2e03a;
  }
  *{margin:0;padding:0;box-sizing:border-box}
  html,body{width:1200px;height:1200px;overflow:hidden;background:var(--backdrop)}
  .canvas{position:relative;width:1200px;height:1200px}
  .card{
    position:absolute;top:453px;width:517px;height:295px;
    background:var(--card-black);overflow:hidden;
    box-shadow:8px 8px 10px rgba(0,0,0,.35);
  }
  .card--front{left:50px}
  .card--back{left:631px}
  .name-frame{
    position:absolute;left:33px;top:34px;width:137px;height:54px;
    border:1px solid var(--gold);
    display:flex;align-items:center;justify-content:center;
    font-family:"Oswald",sans-serif;font-size:28px;color:var(--white);line-height:1;
  }
  .contact-list{position:absolute;left:33px;top:111px;list-style:none}
  .contact-item{
    display:flex;align-items:center;height:21.7px;
    font-family:"Montserrat",sans-serif;font-size:13.6px;color:var(--white);
  }
  .contact-icon{width:14px;height:14px;margin-right:11px;flex:none}
  .address{
    position:absolute;left:33px;top:214px;
    font-family:"Montserrat",sans-serif;font-size:13.6px;line-height:16px;color:var(--address-yellow);
  }
  .brand{position:absolute;font-family:"Oswald",sans-serif;font-weight:400;color:var(--white);line-height:1}
  .card--front .brand-name{left:310px;top:128px;font-size:42px}
  .card--front .brand-tagline{right:31px;top:217px;font-size:26px}
  .card--back .brand-name{left:150px;top:70px;font-size:64px}
  .card--back .brand-tagline{right:130px;top:197px;font-size:38px}
  .gold-band{position:absolute;left:0;bottom:0;width:517px;height:29px;display:block}
</style>
</head>
<body>
<div class="canvas">
  <svg width="0" height="0" style="position:absolute">
    <defs>
      <linearGradient id="goldSheen" x1="0" x2="1" y1="0" y2="0">
        <stop offset="0" stop-color="#f6e27a"/>
        <stop offset=".1" stop-color="#d9a83a"/>
        <stop offset=".14" stop-color="#c1822f"/>
        <stop offset=".45" stop-color="#f4ea74"/>
        <stop offset=".75" stop-color="#fbd24a"/>
        <stop offset=".88" stop-color="#f2c640"/>
        <stop offset=".92" stop-color="#c79035"/>
        <stop offset="1" stop-color="#f4e27a"/>
      </linearGradient>
      <linearGradient id="goldSheenMirror" x1="1" x2="0" y1="0" y2="0">
        <stop offset="0" stop-color="#f6e27a"/>
        <stop offset=".1" stop-color="#d9a83a"/>
        <stop offset=".14" stop-color="#c1822f"/>
        <stop offset=".45" stop-color="#f4ea74"/>
        <stop offset=".75" stop-color="#fbd24a"/>
        <stop offset=".88" stop-color="#f2c640"/>
        <stop offset=".92" stop-color="#c79035"/>
        <stop offset="1" stop-color="#f4e27a"/>
      </linearGradient>
    </defs>
  </svg>

  <section class="card card--front" aria-label="Business card front">
    <div class="name-frame">dr.Ternisu</div>
    <ul class="contact-list">
      <li class="contact-item">
        <svg class="contact-icon" viewBox="0 0 16 16" fill="none" stroke="#f2e03a" stroke-width="1.2"><path d="M3 2l3 0 1 3-2 1.5a8 8 0 0 0 4.5 4.5L11 9l3 1v3a1 1 0 0 1-1 1A11 11 0 0 1 2 3a1 1 0 0 1 1-1z"/></svg>
        +00 000 417 5200
      </li>
      <li class="contact-item">
        <svg class="contact-icon" viewBox="0 0 16 16" fill="none" stroke="#f2e03a" stroke-width="1.2"><rect x="5" y="1.5" width="6" height="13" rx="1"/><line x1="7" y1="12.5" x2="9" y2="12.5"/></svg>
        +00 000 417 5200
      </li>
      <li class="contact-item">
        <svg class="contact-icon" viewBox="0 0 16 16" fill="none" stroke="#f2e03a" stroke-width="1.2"><rect x="1.5" y="4" width="13" height="9"/><path d="M1.5 4l6.5 5 6.5-5"/></svg>
        info@lumendental.com
      </li>
      <li class="contact-item">
        <svg class="contact-icon" viewBox="0 0 16 16" fill="none" stroke="#f2e03a" stroke-width="1.2"><circle cx="8" cy="8" r="6.5"/><ellipse cx="8" cy="8" rx="3" ry="6.5"/><line x1="1.5" y1="8" x2="14.5" y2="8"/></svg>
        info.lumendental.com
      </li>
    </ul>
    <p class="address">118 Harbour Lane<br>london NSW 2000</p>
    <div class="brand brand-name">lumen</div>
    <div class="brand brand-tagline">dental clinic</div>
    <svg class="gold-band" viewBox="0 0 517 29" preserveAspectRatio="none" aria-hidden="true">
      <polygon points="30,0 462,0 447,29 15,29" fill="url(#goldSheen)"/>
      <polygon points="462,0 517,0 517,29 447,29" fill="var(--white)"/>
    </svg>
  </section>

  <section class="card card--back" aria-label="Business card back">
    <div class="brand brand-name">lumen</div>
    <div class="brand brand-tagline">dental clinic</div>
    <svg class="gold-band" viewBox="0 0 517 29" preserveAspectRatio="none" aria-hidden="true">
      <polygon points="0,0 55,0 70,29 0,29" fill="var(--white)"/>
      <polygon points="55,0 486,0 501,29 70,29" fill="url(#goldSheenMirror)"/>
    </svg>
  </section>
</div>
</body>
</html>
```